New Fun, Positive, energised looking Business Card Needed for High Achiever Coach

I am looking for a two sided full colour business card. I am self employed and have recently re branded my 1-2-1 work re-vitalising high achievers. My target client base for these cards is therefore high achievers - usually aged 40 -55, they are often entrepreneurs, CEO or work in banking and finance and 2/3 are male. I work with them on 90 day or 6 month coaching programs to help them live their success in a healthier, more sustainable and fulfiiled way. They pay for this privately so though they are corporate types the cards need not look 'corporate'. I want to portray the idea of transformation, vitality and re-connecting.
You can get a feel for the look I like on my new website: morvenlisk.co.uk
I want to use this logo with strapline (Re-Vitalising High Achievers) (I purchased off Logoharbor) and font/ colours (the turquoise and green).
Details to include on the card:
www.morvenlisk.co.uk
+44 7915 302618
morven@morvenlisk.co.uk
skype: morvenlisk
I'd also like to include:
Do you struggle to switch off? Want to be healthier and feel fitter? Want closer relationships? More clarity over the direction you are headed? I can help you do these things using integrated mind-body techniques. Visit morvenlisk.co.uk TODAY to apply for a FREE Breakthrough session.
BUT if that is too much text for a card I am open to advice/ammendments.
Updates
Thanks for your design - I am considering them. PLease change the wording to :

```html
<!DOCTYPE html>
<html lang="en">
<head>
<meta charset="utf-8">
<title>Morven Lisk – Business Card</title>
<link rel="stylesheet" href="https://fonts.googleapis.com/css2?family=Open+Sans:wght@400;600;700&display=swap">
<style>
  :root {
    --bg: #ecece9;
    --silver-light: #f7f7f6;
    --silver-mid: #e6e6e4;
    --silver-dark: #d4d4d2;
    --green: #4cb84a;
    --turquoise: #1fa8d6;
    --ink: #3f3f3f;
    --rule: #bdbdbb;
    --white: #ffffff;
  }
  * { box-sizing: border-box; margin: 0; padding: 0; }
  html, body {
    width: 1200px; height: 720px; overflow: hidden;
    background: var(--bg);
    font-family: "Open Sans", Arial, sans-serif;
  }
  .canvas {
    position: relative; width: 1200px; height: 720px;
  }
  .card {
    position: absolute; top: 210px;
    width: 525px; height: 300px;
    overflow: hidden;
    background:
      repeating-linear-gradient(0deg, rgba(255,255,255,0.18) 0 1px, rgba(0,0,0,0.02) 1px 3px),
      linear-gradient(160deg, var(--silver-light) 0%, var(--silver-mid) 55%, var(--silver-dark) 100%);
    box-shadow: 0 4px 14px rgba(0,0,0,0.18);
  }
  .card--front { left: 50px; }
  .card--back { left: 625px; }

  .brand {
    position: absolute; display: flex; align-items: center; gap: 8px;
  }
  .brand__mark {
    width: 16px; height: 16px; border-radius: 50%; background: var(--green);
  }
  .brand__name {
    font-weight: 700; font-size: 27px; color: var(--turquoise); letter-spacing: 0.2px;
  }
  .card--front .brand { left: 42px; top: 112px; }
  .card--back .brand { left: 34px; top: 128px; }

  .divider {
    position: absolute; top: 40px; width: 1px; height: 150px; background: var(--rule);
  }
  .card--front .divider { left: 255px; }
  .card--back .divider { left: 240px; top: 40px; height: 200px; }

  .contacts {
    position: absolute; left: 275px; top: 48px; list-style: none;
  }
  .contacts li {
    display: flex; align-items: center; gap: 8px;
    font-size: 14px; color: var(--ink); margin-bottom: 12px;
  }
  .contacts svg { flex: none; }
  .contacts .dot {
    width: 12px; height: 12px; border-radius: 50%; background: var(--turquoise); flex: none;
  }

  .bands { position: absolute; left: 0; bottom: 0; }
  .website {
    position: absolute; right: 34px; bottom: 54px;
    font-size: 15px; font-weight: 700; color: var(--white); letter-spacing: 1px;
  }

  .pitch {
    position: absolute; left: 258px; top: 36px; width: 250px;
    font-size: 12.5px; line-height: 1.55; color: var(--ink);
  }
  .pitch p + p { margin-top: 12px; }
  .pitch strong { font-weight: 700; }
</style>
</head>
<body>
<main class="canvas">

  <section class="card card--front" aria-label="Card front">
    <div class="brand">
      <span class="brand__mark"></span>
      <span class="brand__name">Morven Lisk</span>
    </div>
    <div class="divider"></div>
    <ul class="contacts">
      <li>
        <svg width="12" height="12" viewBox="0 0 12 12" aria-hidden="true"><circle cx="6" cy="6" r="6" fill="var(--turquoise)"/><path d="M3.6 3.2l1.2-.3.6 1.4-.7.5a4 4 0 0 0 1.6 1.6l.5-.7 1.4.6-.3 1.2C5.6 8.2 3.8 6.4 3.6 3.2z" fill="#fff"/></svg>
        +44 7915 302618
      </li>
      <li>
        <svg width="12" height="12" viewBox="0 0 12 12" aria-hidden="true"><circle cx="6" cy="6" r="6" fill="var(--turquoise)"/><rect x="3" y="4" width="6" height="4.2" fill="#fff"/><path d="M3 4l3 2.3L9 4" stroke="var(--turquoise)" stroke-width="0.8" fill="none"/></svg>
        morven@morvenlisk.co.uk
      </li>
      <li><span class="dot"></span>morvenlisk</li>
    </ul>
    <svg class="bands" width="525" height="110" viewBox="0 0 525 110" aria-hidden="true">
      <polygon points="0,92 200,92 250,60 250,76 210,110 0,110" fill="var(--turquoise)"/>
      <polygon points="255,60 290,36 525,36 525,60" fill="var(--green)"/>
    </svg>
    <span class="website">www.morvenlisk.co.uk</span>
  </section>

  <section class="card card--back" aria-label="Card back">
    <div class="brand">
      <span class="brand__mark"></span>
      <span class="brand__name">Morven Lisk</span>
    </div>
    <div class="divider"></div>
    <div class="pitch">
      <p>Do you struggle to switch off?<br>
      Want to be healthier and feel fitter?<br>
      Want closer relationships?<br>
      More clarity over the direction you are headed?</p>
      <p>I can help you do these things using integrated mind-body techniques.</p>
      <p>Visit <strong>morvenlisk.co.uk</strong> TODAY to apply for a FREE Breakthrough session.</p>
    </div>
  </section>

</main>
</body>
</html>
```